Fitness Equipment Repair Business Needs a Catchy New Business Card

We have an existing business card, however, it is quite plain and boring. We are expanding primarily in the commercial area (gyms, studios, apartment complexes etc). The business card will serve as eye candy to those managers/owners that can't be met for a face to face.
Originally I was planning for a brochure as well, but all of our information is better summarized on our website. (brightloopservice.ca).
I would like the card to match the colour scheme of the website and utilize the logo. It should have a professional clean feel to it, however, a little colouring outside the lines wouldn't hurt.
The example card is for my service technician (Colin Marsh). If possible I would like to be able to edit the text to use for more than one person.

Industry/Entity Type

Appliance Repair

Contact Information for Business Card

Clean, crisp and professional but needs to be eye catching. Preferably using the black, white and red colour scheme matching the website. Double sided would be nice, but is not necessary.

Colors
ec1f27
ffffff
000000

Requirements
Must have
• Must be able to edit name, phone number and title to use for multiple people. Must show the company website (brightloopservice.ca).

```html
<!DOCTYPE html>
<html lang="en">
<head>
<meta charset="utf-8">
<title>Brightloop Fitness Service – Business Card</title>
<link rel="stylesheet" href="https://fonts.googleapis.com/css2?family=Roboto+Slab:wght@400;700&display=swap">
<style>
  :root {
    --red: #ec1f27;
    --white: #ffffff;
    --black: #000000;
    --backdrop: #2b2b2b;
    --ink: #1a1a1a;
    --emblem-tone: #3a3a3a;
  }
  * { margin: 0; padding: 0; box-sizing: border-box; }
  html, body { width: 1200px; height: 880px; overflow: hidden; }
  body {
    background: var(--backdrop);
    font-family: "Roboto Slab", Georgia, serif;
    position: relative;
  }
  .card {
    position: absolute;
    width: 560px;
    height: 320px;
    border-radius: 18px;
    overflow: hidden;
    box-shadow: 0 10px 30px rgba(0,0,0,.5);
  }
  /* Front side */
  .card-front {
    left: 70px; top: 80px;
    background: var(--black);
    color: var(--white);
  }
  .emblem {
    position: absolute;
    left: 200px; top: 34px;
    width: 160px; height: 200px;
  }
  .tagline {
    position: absolute;
    left: 0; right: 0; bottom: 34px;
    text-align: center;
    font-size: 14px;
    color: var(--white);
  }
  /* Back side */
  .card-back {
    left: 570px; top: 480px;
    background: var(--white);
  }
  .header-band {
    position: absolute;
    left: 0; top: 0;
    width: 100%; height: 140px;
    background: var(--black);
  }
  .accent-rule {
    position: absolute;
    left: 0; top: 140px;
    width: 100%; height: 7px;
    background: var(--red);
  }
  .company-name {
    position: absolute;
    left: 30px; top: 90px;
    font-size: 24px;
    font-weight: 700;
    font-variant: small-caps;
    letter-spacing: 1px;
    color: var(--white);
    white-space: nowrap;
  }
  .person {
    position: absolute;
    right: 28px; top: 26px;
    text-align: right;
  }
  .person-name { font-size: 19px; color: var(--white); line-height: 1.1; }
  .person-title { font-size: 13px; color: var(--red); }
  .contact {
    position: absolute;
    left: 30px; top: 176px;
    font-size: 13px;
    line-height: 1.4;
    color: var(--ink);
  }
  .address { margin-bottom: 14px; }
  .label { color: var(--red); }
  .website {
    position: absolute;
    right: 28px; top: 216px;
    font-size: 13px;
    color: var(--ink);
  }
  .website .domain { color: var(--red); }
</style>
</head>
<body>
  <section class="card card-front">
    <div class="emblem" role="img" aria-label="Brightloop Fitness Service logo: technician in a hard hat holding a wrench, with the company lettering below">
      <svg width="160" height="200" viewBox="0 0 160 200">
        <rect width="160" height="200" rx="12" fill="var(--emblem-tone)"/>
      </svg>
    </div>
    <p class="tagline">when your equipment can't finish the workout, give us a call !</p>
  </section>

  <section class="card card-back">
    <div class="header-band"></div>
    <div class="accent-rule"></div>
    <h1 class="company-name">Brightloop Fitness Service</h1>
    <div class="person">
      <div class="person-name">Colin Marsh</div>
      <div class="person-title">service technician</div>
    </div>
    <div class="contact">
      <div class="address">1875 Larch Row NW<br>Edmonton AB T6R 2K4</div>
      <div><span class="label">Personal:</span> 578-555-0142</div>
      <div><span class="label">Service Line:</span> 780-555-0187</div>
      <div><span class="label">Service Email:</span> brightloop@mailbox.com</div>
    </div>
    <div class="website">www.<span class="domain">brightloopservice</span>.ca</div>
  </section>
</body>
</html>
```